Lone Star Wetland Flora Stewardship Guild

We need to design the home page of this new website. We would like a fun website design for provides as a resource for members and information for potential members.
Please design so that we can see a portion of background on each side on the website.
I just need the final design files psd no coding needed.
Attached is their logo (colors are not 100% set in stone either so can mess with those as I did in the quick mockup attached)
Attached is a pdf newsletter they send out, you can get a feel for them and what they are about. The design is crappy and we are here to fix that going forward and we are starting with the website.
Here are some quick example websites (design style is open)
- I attached a quick mockup i did just for a content visual but by all means do what you want.
- http://www.brightpathleaders.example/
- http://www.civicunityhub.example/
- http://preview.webskinvault.example/show.php?cat=layouts&host=skinbazaar&temp=novaline
- http://www.meadowkeep.example/
- http://www.urbangleaners.example/
- http://www.projectcozyknit.example/
here are some of the other chapters website (pretty bad!)
and here are some of the others:
- http://www.dwrvcs.example/
- http://kwfg.example/
- http://www.blvcg.example/
Content Items that need to be included:
1. Logo
2. Menu - home, about, members, resources, events, membership, contact
3. Become a member - button or action
4. social links - chatterloop, workweave, clipstream
5. banner - that needs to explain their purpose "Promoting environmental stewardship through operations, research, education and outreach" (or this can be worked into the design)
6. Upcoming event (s)
7. Advertisement - members can place an ad on the website, this can be a placeholder for now
8. newsletter signup
9. advertise with us - this link can be in the footer
30-60 years of age, succesfull (household budgets of 120K+ men and women that live in texas.
Education

```html
<!DOCTYPE html>
<html lang="en">
<head>
<meta charset="utf-8">
<title>Lone Star Wetland Flora Stewardship Guild</title>
<link rel="stylesheet" href="https://fonts.googleapis.com/css2?family=Open+Sans:wght@400;600;700&family=Arimo:wght@400;700&display=swap">
<style>
:root{
  --red:#d8404f;
  --red-text:#cf3a4c;
  --pink:#e35b6c;
  --navy:#0e3170;
  --sky-top:#5a9ad8;
  --sky-low:#d9e9f6;
  --grass:#6fae2c;
  --grass-dark:#3f7a18;
  --footer:#1b1b1b;
  --footer-text:#c9c9c9;
  --body-text:#444;
  --rule:#dedede;
  --white:#fff;
}
*{margin:0;padding:0;box-sizing:border-box}
html,body{width:1071px;height:1200px;overflow:hidden}
body{position:relative;font-family:"Open Sans",sans-serif;color:var(--body-text);
  background:linear-gradient(180deg,var(--sky-top) 0,#8dbbe6 250px,var(--sky-low) 560px,#eef5fa 640px,var(--grass) 700px,var(--grass-dark) 926px,var(--footer) 926px,var(--footer) 100%)}
.abs{position:absolute}
.page{left:126px;top:0;width:820px;height:982px;background:var(--white);border-radius:0 0 4px 4px}
.brand{left:136px;top:40px;display:flex;align-items:center;gap:10px}
.brand-dot{width:30px;height:30px;border-radius:50%;background:var(--navy)}
.brand-name{font-size:13px;font-weight:700;color:var(--navy);line-height:16px;width:170px}
.join-btn{left:777px;top:54px;width:161px;height:35px;background:var(--red);color:var(--white);
  font-size:16px;line-height:35px;text-align:center;border-radius:2px}
.nav{left:126px;top:142px;width:820px;height:36px;background:var(--navy);border-radius:3px 3px 0 0;border-bottom:4px solid var(--red);height:40px}
.nav-item{position:absolute;top:0;height:36px;line-height:36px;color:var(--white);font-size:12.5px;font-weight:600;transform:translateX(-50%)}
.nav-item.active{background:var(--red);top:4px;height:28px;line-height:28px;padding:0 16px;border-radius:2px}
.slider{left:130px;top:186px;width:816px;height:316px;background:#f2f2f2;border-radius:3px;box-shadow:0 6px 10px rgba(0,0,0,.12)}
.slide-photo{left:140px;top:198px;width:792px;height:290px;
  background:linear-gradient(180deg,#9fc3e0 0,#5f9a3e 14%,#3c6b2a 26%,#5e6e5a 40%,#7d8a5a 60%,#96a252 80%,#6e7e3c 100%)}
.slide-caption{left:140px;top:416px;width:792px;height:72px;background:rgba(30,30,40,.72);color:var(--white);
  font-size:14.5px;font-weight:600;line-height:26px;text-align:center;padding-top:10px}
.slider-tab{left:462px;top:482px;width:148px;height:26px;background:#ececec;border-radius:0 0 3px 3px;display:flex;justify-content:center;align-items:center;gap:9px}
.dot{width:8px;height:8px;border-radius:50%;background:#c9c9c9}
.dot.on{background:var(--red)}
.welcome-title{left:126px;top:543px;width:820px;text-align:center;color:var(--red-text);font-size:16px;font-weight:600}
.welcome-text{left:146px;top:570px;width:780px;text-align:center;font-size:11.5px;line-height:24px}
.rule{left:143px;top:668px;width:785px;height:1px;background:var(--rule)}
.section-head{height:36px;border-bottom:1px solid var(--rule);display:flex;justify-content:space-between;align-items:center}
.section-title{color:var(--red-text);font-size:16px;font-weight:400}
.more{font-size:9.5px;font-weight:700;color:#222;border-left:1px solid var(--rule);padding-left:6px;height:22px;line-height:22px;display:flex;align-items:center;gap:6px}
.about{left:143px;top:683px;width:251px}
.about p{font-family:Arimo,sans-serif;font-size:9.6px;line-height:15px;text-align:justify;margin-top:14px;color:#333}
.about p+p{margin-top:15px}
.events{left:416px;top:683px;width:294px}
.event{display:flex;gap:12px;height:75px;border-bottom:1px solid var(--rule);padding-top:12px}
.event:last-child{border-bottom:0}
.event-thumb{width:52px;height:52px;flex:none}
.event-body{font-family:Arimo,sans-serif;font-size:9.6px;line-height:12px;color:#333;text-align:justify}
.read-more{display:block;color:var(--red-text);font-weight:700;margin:5px 0 0 3px}
.ad{left:728px;top:688px;width:200px;height:244px;background:#e6e6e6;border:1px solid #d6d6d6;padding:2px}
.ad-photo{width:100%;height:190px;background:linear-gradient(160deg,#2c5fa8,#1b3f7c 55%,#dfe3ea 56%,#c9ccd4)}
.ad-foot{height:46px;background:#dcdcdc}
.foot-col{top:1001px}
.foot-head{color:var(--pink);font-size:10px;font-weight:700;margin-bottom:10px}
.foot-col a{display:block;color:var(--footer-text);font-family:Arimo,sans-serif;font-size:10.4px;line-height:20px;text-decoration:none}
.foot-col a.see{color:var(--pink);font-weight:700}
.news-label{color:var(--footer-text);font-family:Arimo,sans-serif;font-size:10.4px;line-height:26px}
.field{left:632px;width:136px;height:17px;background:#3a3a3a;border:1px solid #454545}
.signup{left:632px;top:1098px;width:77px;height:26px;background:var(--red);color:var(--white);font-family:Arimo,sans-serif;font-size:12px;line-height:26px;text-align:center}
.social{left:847px;display:flex;align-items:center;gap:13px;color:var(--footer-text);font-family:Arimo,sans-serif;font-size:10.4px}
.social-dot{width:21px;height:21px;border-radius:50%}
.footer-rule{left:0;top:1149px;width:1071px;height:1px;background:#2b2b2b}
.copyright{left:0;top:1170px;width:1071px;text-align:center;color:var(--footer-text);font-family:Arimo,sans-serif;font-size:10px}
</style>
</head>
<body>
<div class="abs page"></div>

<div class="abs brand"><span class="brand-dot"></span><span class="brand-name">Lone Star Wetland Flora Stewardship Guild</span></div>
<div class="abs join-btn">Become a Member</div>

<nav class="abs nav">
  <span class="nav-item active" style="left:38px">HOME</span>
  <span class="nav-item" style="left:146px">ABOUT</span>
  <span class="nav-item" style="left:264px">MEMBERS</span>
  <span class="nav-item" style="left:395px">RESOURCES</span>
  <span class="nav-item" style="left:519px">EVENTS</span>
  <span class="nav-item" style="left:647px">MEMBERSHIP</span>
  <span class="nav-item" style="left:782px">CONTACT</span>
</nav>

<div class="abs slider"></div>
<div class="abs slide-photo" role="img" aria-label="Pond covered with water lily pads, green trees along the far bank"></div>
<div class="abs slide-caption">PROMOTING ENVIRONMENTAL STEWARDSHIP THROUGH OPERATIONS, RESEARCH,<br>EDUCATION AND OUTREACH</div>
<div class="abs slider-tab"><span class="dot on"></span><span class="dot"></span><span class="dot"></span><span class="dot"></span><span class="dot"></span></div>

<h1 class="abs welcome-title">WELCOME TO LSWG</h1>
<p class="abs welcome-text">Lorem ipsum dolor sit amet, consec tetuer adipiscing elit. Praesent vestibulum molestie lacus. Aenean non ummy hendrerit mauris. Phasellus porta. Fusce suscipit varius. mium sociis toque penatibus et magnis dis parturient montes, nascetur ridiculus mus.Lorem ipsum dolor sit amet, consec tetuer adipiscing elit. Praesent vestibulum molestie lacus. Aenean non ummy hendrerit mauris. Phasellus porta.</p>
<div class="abs rule"></div>

<section class="abs about">
  <div class="section-head"><h2 class="section-title">ABOUT US</h2><span class="more">MORE <svg width="7" height="9"><path d="M0 0L7 4.5L0 9Z" fill="#d8404f"/></svg></span></div>
  <p>Sed ut perspiciatis unde omnis iste natus error sit voluptatem accusantium doloremque laudantium, totam rem aperiam, eaque ipsa quae ab illo inventore veritatis et quasi architecto beatae vitae dicta sunt explicabo.</p>
  <p>Nemo enim ipsam voluptatem quia voluptas sit aspernatur aut odit aut fugit, sed quia consequuntur magni dolores eos qui ratione voluptatem sequi nesciunt. Neque porro quisquam est, qui dolorem ipsum quia dolor sit amet, consectetur, adipisci velit,</p>
  <p>sed quia non numquam eius modi tempora incidunt ut labore et dolore magnam aliquam quaerat voluptatem. Ut enim ad minima veniam, quis nostrum exercitationem</p>
</section>

<section class="abs events">
  <div class="section-head"><h2 class="section-title">LATEST EVENT</h2><span class="more">MORE <svg width="7" height="9"><path d="M0 0L7 4.5L0 9Z" fill="#d8404f"/></svg></span></div>
  <div class="event"><div class="event-thumb" role="img" aria-label="Lily pads on still water" style="background:linear-gradient(180deg,#4f7d45,#6f9a7a 50%,#3f6b52)"></div><div class="event-body">ectetur adipisicing elit, sed do eiusmod tempor incididunt ut labore et dolore magna aliqua. Ut enim ad minim veniam, quis nostrud exercitation ullamco<span class="read-more">Read More</span></div></div>
  <div class="event"><div class="event-thumb" role="img" aria-label="Green riverbank with reeds" style="background:linear-gradient(180deg,#dfeaf2,#5f8f3a 40%,#7da6a8 70%,#3d6b2a)"></div><div class="event-body">ectetur adipisicing elit, sed do eiusmod tempor incididunt ut labore et dolore magna aliqua. Ut enim ad minim veniam, quis nostrud exercitation ullamco<span class="read-more">Read More</span></div></div>
  <div class="event"><div class="event-thumb" role="img" aria-label="Open lake under blue sky" style="background:linear-gradient(180deg,#4f8fd0,#b9d6ee 40%,#4f7f3a 55%,#5d86a8 75%,#3d6b2a)"></div><div class="event-body">ectetur adipisicing elit, sed do eiusmod tempor incididunt ut labore et dolore magna aliqua. Ut enim ad minim veniam, quis nostrud exercitation ullamco<span class="read-more">Read More</span></div></div>
</section>

<aside class="abs ad" role="img" aria-label="Member advertisement: PondClear Plus algae treatment by Marshline Supply Co.">
  <div class="ad-photo"></div>
  <div class="ad-foot"></div>
</aside>

<div class="abs foot-col" style="left:143px"><h3 class="foot-head">MENU LINKS</h3><a>Company overview</a><a>Heritage</a><a>Our Team</a><a>Partners</a><a>Privacy</a><a>Sitemap</a></div>
<div class="abs foot-col" style="left:267px"><h3 class="foot-head">ABOUT US</h3><a>Events</a><a>Videos</a><a>Contacts</a><a>Utilities</a><a class="see">SEE MORE</a></div>
<div class="abs foot-col" style="left:386px"><h3 class="foot-head">SUPPORT</h3><a>Press releases</a><a>News stories</a><a>Media downloads</a><a>Awards</a><a>Events</a></div>
<div class="abs foot-col" style="left:525px"><h3 class="foot-head">NEWSLETTER</h3><div class="news-label" style="margin-top:-3px">Name</div><div class="news-label">Last Name</div><div class="news-label">Email</div></div>
<div class="abs field" style="top:1030px"></div>
<div class="abs field" style="top:1053px"></div>
<div class="abs field" style="top:1075px"></div>
<div class="abs signup">SINGUP</div>

<div class="abs foot-col" style="left:847px"><h3 class="foot-head">ADVERTISE WITH US</h3></div>
<div class="abs social" style="top:1026px"><span class="social-dot" style="background:#3b5a9a"></span>Chatterloop</div>
<div class="abs social" style="top:1054px"><span class="social-dot" style="background:#d8302f"></span>Clipstream</div>
<div class="abs social" style="top:1083px"><span class="social-dot" style="background:#2aa3e0"></span>Chirpline</div>
<div class="abs social" style="top:1112px"><span class="social-dot" style="background:#f08a1c"></span>RSS</div>

<div class="abs footer-rule"></div>
<p class="abs copyright">© 2014 LSWG. All Rights Reserved.</p>
</body>
</html>
```